Option Sheet

We need a one page option sheet with a left to right reading of the five options. It should be a one sheet, multiple colors and definitive separations between options This is used in a sales consultation. Backround or colors not in option need to have the follow RGB value (5 red, 20 green, 63 blue)

We added a smaller text file, please change that point

Target Market(s)

Divorce

Industry/Entity Type

Legal

Requirements
Must have
• 1) All five options left to right
• 2)language included in sheet

```html
<!DOCTYPE html>
<html lang="en">
<head>
<meta charset="utf-8">
<title>Divorce – Five Options</title>
<link rel="stylesheet" href="https://fonts.googleapis.com/css2?family=Arimo:ital,wght@0,400;0,700;1,400;1,700&display=swap">
<style>
  :root {
    --navy: rgb(14, 21, 58);
    --white: #ffffff;
    --ink: #000000;
    --sky: #7fd3f5;
    --rose: #f083b1;
    --lemon: #fcef6b;
    --sage: #9ac98b;
    --apricot: #f9c07f;
  }
  html, body {
    margin: 0;
    padding: 0;
    overflow: hidden;
  }
  .sheet {
    position: relative;
    width: 1200px;
    height: 848px;
    background: var(--navy);
    font-family: "Arimo", Arial, sans-serif;
    overflow: hidden;
  }
  .sheet-title {
    position: absolute;
    left: 0;
    right: 0;
    top: 48px;
    margin: 0;
    text-align: center;
    color: var(--white);
    font-size: 99px;
    line-height: 1;
    letter-spacing: -1px;
    text-shadow:
      -1px -1px 0 #cfd3dc,
      2px 2px 0 #8d929d,
      4px 5px 6px rgba(0, 0, 0, 0.75);
    white-space: nowrap;
  }
  .sheet-title .main {
    font-weight: 700;
  }
  .sheet-title .sub {
    font-weight: 400;
    font-style: italic;
    font-size: 92px;
  }
  .option {
    position: absolute;
    top: 188px;
    height: 563px;
    box-sizing: border-box;
    border: 3px solid var(--white);
    box-shadow: 4px 5px 6px rgba(0, 0, 0, 0.6);
    color: var(--ink);
    padding: 8px 0 0 16px;
  }
  .option--nothing   { left: 40px;  width: 171px; background: var(--sky); }
  .option--counsel   { left: 232px; width: 195px; background: var(--rose); }
  .option--diy       { left: 448px; width: 229px; background: var(--lemon); }
  .option--limited   { left: 698px; width: 275px; background: var(--sage); }
  .option--hire      { left: 994px; width: 168px; background: var(--apricot); }

  .option-number {
    margin: 0 16px 0 0;
    text-align: center;
    font-weight: 700;
    font-style: italic;
    font-size: 23px;
    line-height: 1.2;
  }
  .option-name {
    margin: 2px 16px 9px 0;
    text-align: center;
    font-weight: 700;
    font-size: 28px;
    line-height: 1.02;
    letter-spacing: -0.3px;
  }
  .option--nothing .option-name { margin-left: -10px; margin-right: 0; }
  .group-label {
    margin: 0 0 4px 2px;
    font-weight: 700;
    font-style: italic;
    font-size: 18px;
    line-height: 1.2;
  }
  .points {
    list-style: none;
    margin: 0 0 7px 0;
    padding: 0;
  }
  .points li {
    position: relative;
    padding-left: 19px;
    font-size: 17px;
    line-height: 22.4px;
    margin-bottom: 4px;
    padding-right: 4px;
  }
  .points li::before {
    content: "";
    position: absolute;
    left: 2px;
    top: 5px;
    width: 10px;
    height: 10px;
    border: 2px solid var(--ink);
    border-radius: 50%;
    box-sizing: border-box;
    box-shadow: 1.5px 1px 0 var(--ink);
  }
</style>
</head>
<body>
<main class="sheet">
  <h1 class="sheet-title"><span class="main">DIVORCE</span> <span class="sub">(Five Options)</span></h1>

  <section class="option option--nothing">
    <p class="option-number">Option #1:</p>
    <h2 class="option-name">Do Nothing</h2>
    <p class="group-label">Advantages:</p>
    <ul class="points">
      <li>Stay married</li>
      <li>No life<br>Changes</li>
    </ul>
    <p class="group-label">Disadvantages:</p>
    <ul class="points">
      <li>Remain unhappy, depressed, anxious</li>
      <li>Money and assets may disappear</li>
      <li>What is going to change?</li>
    </ul>
  </section>

  <section class="option option--counsel">
    <p class="option-number">Option #2:</p>
    <h2 class="option-name">Go to<br>Counseling</h2>
    <p class="group-label">Advantages:</p>
    <ul class="points">
      <li>Reconcile marriage</li>
      <li>Help make<br>a better life</li>
    </ul>
    <p class="group-label">Disadvantages:</p>
    <ul class="points">
      <li>Past issues are highlighted and may drudge up old wounds</li>
      <li>It may just clarify the reasons you need to separate and/or divorce</li>
      <li>Both parties must be invested and willing to participate</li>
    </ul>
  </section>

  <section class="option option--diy">
    <p class="option-number">Option #3:</p>
    <h2 class="option-name">Do it Yourself</h2>
    <p class="group-label">Advantages:</p>
    <ul class="points">
      <li>No attorney fees</li>
      <li>You are your on attorney</li>
    </ul>
    <p class="group-label">Disadvantages:</p>
    <ul class="points">
      <li>People often find that what is “fair,” may in fact, not be truly fair</li>
      <li>Often times, people do not know the risks</li>
      <li>Complicated legal system within intrigue rules</li>
      <li>Unsure how to complete the necessary paperwork and meet the deadlines</li>
    </ul>
  </section>

  <section class="option option--limited">
    <p class="option-number">Option #4:</p>
    <h2 class="option-name">Limited<br>Representation</h2>
    <p class="group-label">Advantages:</p>
    <ul class="points">
      <li>Balance between going alone and our limited involvement in the case</li>
    </ul>
    <p class="group-label">Disadvantages:</p>
    <ul class="points">
      <li>Our terms may not benefit from our legal knowledge</li>
      <li>The legal consequences of your legal documents will not be explained to you so that you can formulate a plan for handling the rest of your case.</li>
      <li>Your spouse or other parties may cause your legal fees to increase significantly without action on your part</li>
    </ul>
  </section>

  <section class="option option--hire">
    <p class="option-number">Option #5:</p>
    <h2 class="option-name">Hire Us</h2>
    <p class="group-label">Advantages:</p>
    <ul class="points">
      <li>Gain the full benefits of our experience</li>
      <li>Have a team of Family Law focus attorneys</li>
      <li>Often saves you or makes you money in the long run</li>
      <li>Save you time, energy and stress</li>
    </ul>
    <p class="group-label">Disadvantages:</p>
    <ul class="points">
      <li>Initial cost</li>
    </ul>
  </section>
</main>
</body>
</html>
```